Unique Business Card Design

Unique Business Card design for our orthotic and prosthetic company. Our logo is on our website, color is light blue. Unique shape (artificial leg shaped, vertical, etc..) preferred. Logo, business name, individual name and basic demographics needed.

Industry/Entity Type

Business

Contact Information for Business Card

Logo, Industry, Phone # Logo, "Prosthetic & Orthotic Services" Place to add individual name and contact info

Colors
cee9f5

Requirements
Must have
• The icon must be there, placement of "Prosthetic & Orthotic Services" can be moved
Nice to have
• Like the mix of light blue, and a little darker blue. One design included the icons from my website which was a nice touch

```html
<!DOCTYPE html>
<html lang="en">
<head>
<meta charset="utf-8">
<title>Limbwell Inc. Business Card</title>
<link rel="stylesheet" href="https://fonts.googleapis.com/css2?family=Open+Sans:wght@600&family=Roboto:wght@400;500&display=swap">
<style>
  :root {
    --backdrop: #3b3b3b;
    --brand-blue: #0b5bab;
    --brand-blue-light: #1a6bbb;
    --accent-blue: #1d5fae;
    --card-white: #ffffff;
    --text-gray: #555555;
    --rule-gray: #d9d9d9;
  }
  * { margin: 0; padding: 0; box-sizing: border-box; }
  html, body { width: 1200px; height: 1000px; overflow: hidden; }
  body { background: var(--backdrop); position: relative; font-family: "Roboto", Arial, sans-serif; }

  .card { position: absolute; left: 220px; width: 760px; height: 434px; border-radius: 28px; overflow: hidden; }

  /* Front */
  .card-front { top: 50px; background: linear-gradient(120deg, var(--brand-blue) 0%, var(--brand-blue) 55%, var(--brand-blue-light) 100%); color: var(--card-white); }
  .front-mark { position: absolute; left: 122px; top: 147px; width: 140px; height: 140px; border-radius: 50%; background: var(--card-white); }
  .front-name { position: absolute; left: 280px; top: 168px; font-family: "Open Sans", Arial, sans-serif; font-weight: 600; font-size: 39px; letter-spacing: 0.5px; white-space: nowrap; }
  .front-tagline { position: absolute; left: 300px; top: 229px; font-size: 22px; white-space: nowrap; }
  .front-web { position: absolute; left: 0; right: 0; top: 374px; text-align: center; font-family: "Open Sans", Arial, sans-serif; font-weight: 600; font-size: 16px; }

  /* Back */
  .card-back { top: 524px; background: var(--card-white); }
  .back-mark { position: absolute; left: 91px; top: 73px; width: 260px; height: 260px; border-radius: 50%; background: var(--brand-blue); }
  .back-divider { position: absolute; left: 375px; top: 94px; width: 1px; height: 248px; background: var(--rule-gray); }
  .contact { position: absolute; left: 398px; top: 88px; color: var(--text-gray); font-size: 17px; line-height: 22px; }
  .contact-name { color: var(--accent-blue); font-weight: 500; font-size: 24px; line-height: 30px; }
  .contact-role { margin-bottom: 14px; }
  .contact-company { color: var(--accent-blue); }
  .contact-address { margin-bottom: 12px; }
  .contact-line { display: flex; align-items: center; gap: 6px; height: 24.5px; }
  .contact-line svg { width: 14px; height: 14px; fill: var(--accent-blue); flex: none; }
  .web-domain { color: var(--accent-blue); }
  .back-rule { position: absolute; left: 0; right: 0; bottom: 20px; height: 2px; background: var(--rule-gray); }
  .back-band { position: absolute; left: 0; right: 0; bottom: 0; height: 16px; background: var(--brand-blue); }
</style>
</head>
<body>
  <section class="card card-front">
    <div class="front-mark"></div>
    <div class="front-name">LIMBWELL INC.</div>
    <div class="front-tagline">Prosthetic &amp; Orthotic Services</div>
    <div class="front-web">www.limbwellinc.com</div>
  </section>

  <section class="card card-back">
    <div class="back-mark"></div>
    <div class="back-divider"></div>
    <div class="contact">
      <div class="contact-name">Mara Ellison</div>
      <div class="contact-role">CO LPO</div>
      <div class="contact-company">LIMBWELL INC.</div>
      <div class="contact-address">820 Harbor Lane<br>Easton, NY 11000</div>
      <div class="contact-line">
        <svg viewBox="0 0 14 14"><path d="M4 0h6a1 1 0 0 1 1 1v12a1 1 0 0 1-1 1H4a1 1 0 0 1-1-1V1a1 1 0 0 1 1-1zm.5 1.5v9h5v-9zM7 11.5a.8.8 0 1 0 0 1.6.8.8 0 0 0 0-1.6z"/></svg>
        <span>845-5550142</span>
      </div>
      <div class="contact-line">
        <svg viewBox="0 0 14 14"><path d="M3 1l2.5 2.5-1.5 2a8 8 0 0 0 4.5 4.5l2-1.5L13 11l-1.5 2C6 13 1 8 1 2.5z"/></svg>
        <span>(718) 555-0170</span>
      </div>
      <div class="contact-line">
        <svg viewBox="0 0 14 14"><path d="M3 1h8v3H3zM1 5h12v6h-2V9H3v2H1zm3 5h6v3H4z"/></svg>
        <span>(718) 555-0191</span>
      </div>
      <div class="contact-line">
        <svg viewBox="0 0 14 14"><path d="M1 3h12v1L7 8 1 4zm0 2.3l6 4 6-4V11H1z"/></svg>
        <span>Mellison@limbwellinc.com</span>
      </div>
      <div class="contact-line">
        <svg viewBox="0 0 14 14"><path d="M7 1a6 6 0 1 0 0 12A6 6 0 0 0 7 1zm0 1.2c.7.8 1.2 2 1.4 3.3H5.6C5.8 4.2 6.3 3 7 2.2zM2.3 6.5h2.2c0 .4 0 .7.1 1H2.3a4.8 4.8 0 0 1 0-1zm3.3 0h2.8v1H5.6zm3.9 0h2.2a4.8 4.8 0 0 1 0 1H9.5c.1-.3.1-.6 0-1zM5.6 8.5h2.8C8.2 9.8 7.7 11 7 11.8c-.7-.8-1.2-2-1.4-3.3z"/></svg>
        <span>www.<span class="web-domain">limbwellinc</span>.net</span>
      </div>
    </div>
    <div class="back-rule"></div>
    <div class="back-band"></div>
  </section>
</body>
</html>
```